Sign for Truck Parking Company

We do not like the proposed solution of a local signage company.

We need to use the existing sign in terms of size. We want to use our logo, tag line "Nationwide Trailer Parking Solutions", show our phone as (970) BRELMAX & (970) 555-0143, our address of 2840 Alder and our url of halvenmoorgroup.com. We want to make sure the fonts match our corporate logo as best as possible. We don't like the current layout as the fonts don't match and it looks very busy. You can assume that the base will be painted black. Can we make “Nationwide Trailer Parking Solutions” roughly the same font, size and color as the URL (and maybe make it the same size and font and color as “Companies” by shrinking the logo a little).I think on the phone number, its letter equivalent can be on the bottom portion. We are up for a variety of options and want to maintain our fonts and colors. Thanks!

```html
<!DOCTYPE html>
<html lang="en">
<head>
<meta charset="utf-8">
<title>Halvenmoor Group – Parking Sign Options</title>
<link href="https://fonts.googleapis.com/css2?family=Michroma&display=swap" rel="stylesheet">
<style>
  :root{
    --sign-black:#000000;
    --sign-white:#ffffff;
    --brand-blue:#2c5ea5;
    --brand-gray:#707074;
  }
  html,body{margin:0;padding:0;overflow:hidden;background:var(--sign-white);}
  .artboard{display:block;width:1200px;height:1200px;}
  .sign-text{font-family:'Michroma',sans-serif;}
  .fill-black{fill:var(--sign-black);}
  .fill-white{fill:var(--sign-white);}
  .fill-blue{fill:var(--brand-blue);}
  .fill-gray{fill:var(--brand-gray);}
  .frame-line{fill:none;stroke:var(--brand-blue);stroke-width:3.5;}
  .tagline{fill:var(--sign-white);}
  .phone{fill:var(--sign-white);}
  .url{fill:var(--brand-gray);}
  .address{fill:var(--sign-white);}
  .brand-name{fill:var(--brand-blue);}
</style>
</head>
<body>
<svg class="artboard" viewBox="0 0 1500 1500" xmlns="http://www.w3.org/2000/svg">

  <!-- Wide sign option -->
  <g class="sign sign--wide">
    <rect class="fill-black" x="204" y="163" width="1091" height="551"/>
    <rect class="fill-white" x="224" y="184" width="1052" height="509"/>
    <polygon class="fill-gray" points="788,184 1276,184 1276,558 1256,558 1256,505 922,505"/>
    <polygon class="fill-gray" points="275,505 1256,505 1256,558 247,558"/>
    <polygon class="fill-blue" points="930,560 1276,560 1276,693 872,693"/>
    <rect class="frame-line" x="244" y="207" width="1012" height="462"/>

    <g class="brand sign-text">
      <rect class="fill-blue" x="310" y="318" width="34" height="34"/>
      <text class="brand-name" x="358" y="352" font-size="44" textLength="372" lengthAdjust="spacingAndGlyphs">HALVENMOOR</text>
      <text class="brand-name" x="310" y="462" font-size="44" textLength="420" lengthAdjust="spacing">GROUP</text>
    </g>

    <g class="sign-text tagline" text-anchor="end" font-size="37">
      <text x="1213" y="313" textLength="320" lengthAdjust="spacingAndGlyphs">NATIONWIDE</text>
      <text x="1213" y="360" textLength="208" lengthAdjust="spacingAndGlyphs">TRAILER</text>
      <text x="1213" y="406" textLength="225" lengthAdjust="spacingAndGlyphs">PARKING</text>
      <text x="1213" y="453" textLength="290" lengthAdjust="spacingAndGlyphs">SOLUTIONS</text>
    </g>

    <text class="sign-text phone" x="308" y="546" font-size="37" textLength="902" lengthAdjust="spacingAndGlyphs">(970) BRELMAX • (970) 555-0143</text>
    <text class="sign-text url" x="310" y="620" font-size="30" textLength="570" lengthAdjust="spacingAndGlyphs">halvenmoorgroup.com</text>
    <text class="sign-text address" x="952" y="623" font-size="34" textLength="260" lengthAdjust="spacingAndGlyphs">2840 Alder</text>
  </g>

  <!-- Compact sign option -->
  <g class="sign sign--compact">
    <rect class="fill-black" x="357" y="831" width="786" height="505"/>
    <rect class="fill-white" x="372" y="851" width="756" height="362"/>
    <rect class="fill-white" x="372" y="1227" width="756" height="95"/>
    <polygon class="fill-gray" points="742,851 1128,851 1128,1198 1111,1198 1111,1148 866,1148"/>
    <polygon class="fill-gray" points="420,1148 1111,1148 1111,1197 395,1197"/>
    <polygon class="fill-blue" points="873,1227 1128,1227 1128,1322 820,1322"/>
    <rect class="frame-line" x="388.5" y="872" width="722" height="325"/>

    <g class="brand sign-text">
      <rect class="fill-blue" x="417" y="985" width="28" height="28"/>
      <text class="brand-name" x="456" y="1013" font-size="36" textLength="307" lengthAdjust="spacingAndGlyphs">HALVENMOOR</text>
      <text class="brand-name" x="417" y="1099" font-size="36" textLength="346" lengthAdjust="spacing">GROUP</text>
    </g>

    <g class="sign-text tagline" text-anchor="end" font-size="28">
      <text x="1088" y="968" textLength="260" lengthAdjust="spacingAndGlyphs">NATIONWIDE</text>
      <text x="1088" y="1006" textLength="168" lengthAdjust="spacingAndGlyphs">TRAILER</text>
      <text x="1088" y="1044" textLength="183" lengthAdjust="spacingAndGlyphs">PARKING</text>
      <text x="1088" y="1082" textLength="236" lengthAdjust="spacingAndGlyphs">SOLUTIONS</text>
    </g>

    <text class="sign-text phone" x="433" y="1184" font-size="27" textLength="652" lengthAdjust="spacingAndGlyphs">(970) BRELMAX • (970) 555-0143</text>
    <text class="sign-text url" x="403" y="1284" font-size="23" textLength="427" lengthAdjust="spacingAndGlyphs">halvenmoorgroup.com</text>
    <text class="sign-text address" x="888" y="1286" font-size="26" textLength="198" lengthAdjust="spacingAndGlyphs">2840 Alder</text>
  </g>
</svg>
</body>
</html>
```